Investment company needing business card

We are wanting a business card which looks sharp and easy on the eye. We are thinking of having a business card with the logo embossed on it, to really make it stand out. We will only have a small amount of information of the business card, person's name, position, email address and phone number

Contact Information for Business Card

Danielle Frost
Executive Assistant
+64 21 473 5162
danielf@harwickpartners.co.nz

Requirements
Must have
• Embossed logo
Should not have
• Not to be busy

```html
<!DOCTYPE html>
<html lang="en">
<head>
<meta charset="utf-8">
<title>Harwick Partners – Business Card</title>
<link href="https://fonts.googleapis.com/css2?family=Roboto+Condensed:wght@400;700&family=Roboto:wght@400&display=swap" rel="stylesheet">
<style>
  :root {
    --backdrop: #1f1f1f;
    --card: #f1f1f1;
    --brand-green: #22b573;
    --text-grey: #555555;
    --mark-grey: #5f5f5f;
  }
  html, body {
    margin: 0;
    padding: 0;
    width: 1200px;
    height: 960px;
    overflow: hidden;
    background: var(--backdrop);
  }
  .business-card {
    position: absolute;
    left: 300px;
    top: 309px;
    width: 600px;
    height: 343px;
    background: var(--card);
    border-radius: 18px;
  }
  .brand {
    position: absolute;
    right: 36px;
    top: 30px;
    display: flex;
    align-items: center;
    gap: 10px;
  }
  .brand-square {
    width: 30px;
    height: 30px;
    background: var(--mark-grey);
  }
  .brand-name {
    font-family: "Roboto Condensed", sans-serif;
    font-weight: 700;
    font-size: 24px;
    letter-spacing: 0.5px;
    color: var(--brand-green);
    line-height: 1;
  }
  .person {
    position: absolute;
    left: 35px;
    top: 210px;
  }
  .person-name {
    margin: 0;
    font-family: "Roboto Condensed", sans-serif;
    font-weight: 700;
    font-size: 23px;
    line-height: 26px;
    color: var(--brand-green);
  }
  .person-role {
    margin: 0 0 10px;
    font-family: "Roboto Condensed", sans-serif;
    font-weight: 400;
    font-size: 16px;
    line-height: 20px;
    color: var(--text-grey);
  }
  .contact-list {
    margin: 0;
    padding: 0;
    list-style: none;
    font-family: "Roboto", sans-serif;
    font-size: 14.5px;
    line-height: 18px;
    color: var(--text-grey);
  }
</style>
</head>
<body>
  <div class="business-card">
    <div class="brand">
      <span class="brand-square"></span>
      <span class="brand-name">HARWICK PARTNERS</span>
    </div>
    <div class="person">
      <h1 class="person-name">DANIELLE FROST</h1>
      <p class="person-role">EXECUTIVE ASSISTANT</p>
      <ul class="contact-list">
        <li class="contact-phone">+64 21 473 5162</li>
        <li class="contact-email">danielf@harwickpartners.co.nz</li>
        <li class="contact-web">www.harwickpartners.co.nz</li>
      </ul>
    </div>
  </div>
</body>
</html>
```